Home Security Company Business Card

Looking for a eye catching business card that is non traditional and stands out but yet still looks professional. It should include all the pertinent information such as name, title, address, telephone, e-mail, website address should definitely stand out and then finally the logo.

Target Market(s)

Residential and Commercial accounts mostly upscale accounts

Industry/Entity Type

Security

Contact Information for Business Card

Name
Title
Address
Office #
Cell #
E-mail
Website

Font styles to use
Serif
Sans Serif

Requirements
Must have
• Logo, two sided color configuration
Nice to have
• You decide
Should not have
• There really aren't any.

```html
<!DOCTYPE html>
<html lang="en">
<head>
<meta charset="utf-8">
<title>Hartwell Protection Group – Business Card</title>
<link rel="stylesheet" href="https://fonts.googleapis.com/css2?family=Cormorant+Garamond:wght@600&family=Noto+Serif:wght@400&display=swap">
<style>
  :root {
    --burgundy: #7b1418;
    --gold: #e2b64a;
    --white: #ffffff;
    --backdrop: #efe6d6;
    --divider: #a34a4c;
  }
  * { margin: 0; padding: 0; box-sizing: border-box; }
  html, body { width: 1189px; height: 1200px; overflow: hidden; }
  body { background: var(--backdrop); position: relative; }

  .card {
    position: absolute;
    left: 171px;
    width: 856px;
    height: 487px;
    border-radius: 22px;
    box-shadow: 4px 8px 14px rgba(0,0,0,0.28);
  }
  .card--front { top: 68px; background: var(--burgundy); }
  .card--back { top: 627px; background: var(--white); }

  .wordmark {
    position: absolute;
    font-family: "Cormorant Garamond", serif;
    font-weight: 600;
    text-align: center;
    line-height: 1;
  }
  .wordmark__main { display: block; }
  .wordmark__sub { display: block; }

  .card--front .wordmark {
    color: var(--white);
    left: 0; right: 0; top: 180px;
  }
  .card--front .wordmark__main { font-size: 86px; letter-spacing: 1px; }
  .card--front .wordmark__sub { font-size: 40px; margin-top: 2px; letter-spacing: 0.5px; }

  .card--back .wordmark {
    color: var(--burgundy);
    left: 60px; width: 340px; top: 195px;
  }
  .card--back .wordmark__main { font-size: 50px; }
  .card--back .wordmark__sub { font-size: 23px; margin-top: 2px; }

  .divider {
    position: absolute;
    left: 423px; top: 95px;
    width: 1.5px; height: 290px;
    background: var(--divider);
  }

  .contact {
    position: absolute;
    left: 464px; top: 100px;
    font-family: "Noto Serif", serif;
    color: var(--burgundy);
  }
  .contact__name {
    font-family: "Cormorant Garamond", serif;
    font-weight: 600;
    font-size: 38px;
    line-height: 1;
  }
  .contact__title {
    font-size: 20px;
    color: var(--gold);
    letter-spacing: 1px;
    line-height: 1;
    margin-top: 0;
  }
  .contact__address {
    font-size: 21px;
    line-height: 28px;
    margin-top: 28px;
    letter-spacing: 0.3px;
  }
  .contact__lines { list-style: none; margin-top: 12px; }
  .contact__line {
    display: flex; align-items: center;
    font-size: 20px; height: 31.5px; letter-spacing: 0.5px;
  }
  .icon {
    width: 23px; height: 23px; margin-right: 16px;
    flex-shrink: 0;
  }
  .contact__web {
    font-size: 19px;
    color: var(--gold);
    letter-spacing: 1.5px;
    margin-top: 20px;
  }
</style>
</head>
<body>
  <section class="card card--front" aria-label="Card front">
    <p class="wordmark">
      <span class="wordmark__main">HARTWELL</span>
      <span class="wordmark__sub">PROTECTION GROUP INC.</span>
    </p>
  </section>

  <section class="card card--back" aria-label="Card back">
    <p class="wordmark">
      <span class="wordmark__main">HARTWELL</span>
      <span class="wordmark__sub">PROTECTION GROUP INC.</span>
    </p>
    <div class="divider"></div>
    <div class="contact">
      <p class="contact__name">Marcus Reed</p>
      <p class="contact__title">Owner</p>
      <p class="contact__address">PO Box your address<br>2nd Lane, WA 0000 USA</p>
      <ul class="contact__lines">
        <li class="contact__line">
          <svg class="icon" viewBox="0 0 24 24" aria-hidden="true">
            <rect width="24" height="24" rx="4" fill="#e2b64a"/>
            <path d="M5 10c0-3 14-3 14 0v1h-4v-1.5H9V11H5z" fill="#fff"/>
            <rect x="7" y="12" width="10" height="6" rx="1" fill="#fff"/>
          </svg>555-014-2286
        </li>
        <li class="contact__line">
          <svg class="icon" viewBox="0 0 24 24" aria-hidden="true">
            <rect width="24" height="24" rx="4" fill="#e2b64a"/>
            <rect x="8" y="4" width="8" height="16" rx="1.5" fill="#fff"/>
            <rect x="9.5" y="6" width="5" height="5" fill="#e2b64a"/>
          </svg>+1 555-014-2290
        </li>
        <li class="contact__line">
          <svg class="icon" viewBox="0 0 24 24" aria-hidden="true">
            <rect width="24" height="24" rx="4" fill="#e2b64a"/>
            <rect x="4.5" y="7" width="15" height="10" fill="none" stroke="#fff" stroke-width="1.6"/>
            <path d="M4.5 7l7.5 6 7.5-6M4.5 17l5.5-5M19.5 17l-5.5-5" fill="none" stroke="#fff" stroke-width="1.4"/>
          </svg>info@hartwellpg.com
        </li>
      </ul>
      <p class="contact__web">www.hartwellpg.com</p>
    </div>
  </section>
</body>
</html>
```